WordPress Design for both website and landing page for an expert

I need a clean and stylish design for my new website. I work as an expert (see attached file WHY HOW WHAT), my product is expert opinion (reports) for company evaluations You can use all of the attached pictures colored or black / white. The person is me, you can add other pictures, if you want. The design should be clean and stylish, so you could use white, black, gray, silver and / or one additional color. I have added an idea about my website, see attached file CONCEPT WEBSITE If you have any more information, please do not hesitate to contact us 'Hesitate to ask me ...

```html
<!DOCTYPE html>
<html lang="de">
<head>
<meta charset="utf-8">
<title>Arno Velden – Sachverständiger für Firmenbewertungen</title>
<link href="https://fonts.googleapis.com/css2?family=Montserrat:wght@400;500;600;700&family=Roboto:wght@400;500;700&display=swap" rel="stylesheet">
<style>
:root{
  --black:#000;
  --ink:#111;
  --dark:#2b2b2b;
  --mid:#3d3d3d;
  --grey:#8a8a8a;
  --light:#ededed;
  --white:#fff;
  --silver:#b9bec4;
  --text:#333;
  --partner-blue:#3f5d86;
}
*{box-sizing:border-box;margin:0;padding:0}
html,body{width:1200px;height:5028px;overflow:hidden}
body{font-family:"Roboto",Arial,sans-serif;color:var(--text);background:var(--white);position:relative}
h1,h2,h3,h4,.brand,.num{font-family:"Montserrat",Arial,sans-serif}
section,header,footer{position:absolute;left:0;width:1200px}

/* hero */
.hero{top:0;height:720px;background:linear-gradient(100deg,#2c2f33 0%,#6b7076 45%,#c9ccd0 70%,#9aa0a6 100%);}
.hero-photo{position:absolute;left:460px;top:110px;width:360px;height:610px;background:linear-gradient(180deg,#3b3d40,#151617);opacity:.85}
.topbar{position:absolute;top:0;left:0;width:1200px;height:150px;background:linear-gradient(180deg,rgba(0,0,0,.85),rgba(0,0,0,0))}
.brand{position:absolute;left:94px;top:48px;color:var(--white);font-weight:500;font-size:30px;letter-spacing:6px;text-transform:uppercase;display:flex;align-items:center;gap:14px}
.brand .dot{width:18px;height:18px;border-radius:50%;background:var(--silver)}
.nav{position:absolute;right:92px;top:62px;display:flex;gap:30px}
.nav a{color:var(--white);text-decoration:none;font-size:16px;font-weight:500}
.hero h1{position:absolute;left:94px;top:345px;color:var(--white);font-size:56px;line-height:66px;font-weight:700}
.hero p{position:absolute;left:94px;top:495px;color:var(--white);font-size:17px}

/* uses */
.uses{top:720px;height:537px;background:linear-gradient(180deg,#4a4a4a,#2f2f2f 60%,#3a3a3a)}
.uses h2{position:absolute;top:80px;width:100%;text-align:center;color:var(--white);font-size:36px;font-weight:600}
.use-list{position:absolute;left:302px;top:205px;width:613px;list-style:none}
.use-list li{height:60px;background:var(--white);border-radius:6px;margin-bottom:26px;padding-left:26px;line-height:60px;font-family:"Montserrat",sans-serif;font-weight:600;font-size:17px;color:var(--ink)}

/* reasons */
.reasons{top:1257px;height:553px;background:var(--black);color:var(--white)}
.reasons h2{position:absolute;top:50px;width:100%;text-align:center;font-size:36px;font-weight:600}
.reason{position:absolute;top:140px;width:300px;text-align:center}
.reason svg{display:block;margin:0 auto;width:124px;height:124px}
.reason .num{font-size:64px;font-weight:500;line-height:70px;margin-top:14px}
.reason h3{font-size:22px;font-weight:600;margin-top:2px;color:var(--white)}
.reason p{font-size:14px;line-height:21px;margin:16px auto 0;width:250px;color:#ddd}
.connector{position:absolute;top:200px;height:3px;width:160px;background:var(--white)}

/* promise */
.promise{top:1810px;height:480px;background:var(--white);text-align:center}
.promise .mark{position:absolute;top:125px;width:100%;font-family:"Montserrat",sans-serif;font-size:40px;font-weight:600;color:var(--grey);letter-spacing:4px}
.promise h2{position:absolute;top:245px;width:100%;font-size:26px;font-weight:600;color:var(--ink)}
.promise p{position:absolute;top:305px;width:100%;font-size:17px;line-height:28px;color:#444}

/* why how what */
.whw{top:2290px;height:988px;background:var(--light)}
.whw-track{position:absolute;left:303px;top:195px;width:3px;height:640px;background:var(--ink)}
.ring{position:absolute;left:181px;width:248px;height:248px;border-radius:50%;background:var(--ink);display:flex;align-items:center;justify-content:center}
.ring .inner{width:162px;height:162px;border-radius:50%;background:var(--white);border:14px solid var(--ink);outline:3px solid var(--white);outline-offset:-32px;display:flex;align-items:center;justify-content:center;font-family:"Montserrat",sans-serif;font-weight:700;font-size:30px;color:var(--ink)}
.ring-dot{position:absolute;left:296px;width:16px;height:16px;border-radius:50%;background:var(--ink)}
.whw-text{position:absolute;left:600px;width:400px;text-align:center}
.whw-text h3{font-size:34px;font-weight:600;color:var(--ink)}
.whw-text p{margin-top:24px;font-size:17px;line-height:26px;color:#333}

/* about */
.about{top:3278px;height:788px;background:var(--white)}
.about h2{position:absolute;left:536px;top:140px;width:640px;text-align:center;font-size:34px;font-weight:600;color:var(--ink)}
.about-photo{position:absolute;left:94px;top:292px;width:436px;height:346px;background:linear-gradient(120deg,#f1f1f1,#cfd2d5 55%,#8d9196)}
.about-frame{position:absolute;left:138px;top:268px;width:300px;height:390px;border:3px solid var(--ink)}
.about-card{position:absolute;left:536px;top:208px;width:572px;height:470px;background:var(--white);box-shadow:0 4px 20px rgba(0,0,0,.14);font-size:13.5px;line-height:19px;color:#222}
.about-card h4{font-size:14px;font-weight:700;margin-bottom:12px;color:var(--ink)}
.col-main{position:absolute;left:24px;top:30px;width:330px}
.col-side{position:absolute;left:394px;top:30px;width:160px}
.block{margin-bottom:44px}
.badge{width:150px;height:40px;background:var(--partner-blue);margin-bottom:12px}
.badge.small{width:120px;height:34px;background:var(--silver)}

/* contact */
.contact{top:4066px;height:576px;background:linear-gradient(180deg,#5a5a5a,#3a3a3a 55%,#4c4c4c)}
.contact h2{position:absolute;top:90px;width:100%;text-align:center;font-size:38px;font-weight:600;color:var(--white)}
.field{position:absolute;height:40px;background:var(--white);font-size:14px;color:#333;padding:11px 12px}
.field.tall{height:108px}
.submit{position:absolute;left:530px;top:426px;width:124px;height:40px;background:var(--black);color:var(--white);font-size:16px;text-align:center;line-height:40px}

/* footer */
.footer{top:4642px;height:386px;background:var(--black);color:var(--white)}
.footer .brand{position:absolute;left:94px;top:150px}
.footer h3{font-size:28px;font-weight:600}
.links{position:absolute;left:486px;top:60px}
.links ul{list-style:none;margin-top:16px}
.links li{font-size:16px;line-height:33px}
.news{position:absolute;left:764px;top:60px;width:260px}
.news p{margin-top:16px;font-size:16px;line-height:26px}
.news .in{margin-top:14px;width:200px;height:34px;background:var(--white);color:#333;font-size:12px;padding:10px}
.news .btn{margin-top:14px;width:80px;height:32px;background:var(--white);color:var(--ink);font-size:15px;text-align:center;line-height:32px}
.copy{position:absolute;top:336px;width:100%;text-align:center;font-size:14px;color:#ddd}
</style>
</head>
<body>

<section class="hero">
  <div class="hero-photo" role="img" aria-label="Portrait des Sachverständigen im Anzug in einem hellen Büro"></div>
  <div class="topbar"></div>
  <div class="brand"><span class="dot"></span>Arno Velden</div>
  <nav class="nav"><a>Home</a><a>What I Do</a><a>Why I Do It &amp; How I Do It</a><a>About Me</a><a>Contact</a></nav>
  <h1>Sachverständiger für<br>Firmenbewertungen</h1>
  <p>Sie benötigen ein Gutachten zur Ermittlung des Wertes Ihres Unternehmens</p>
</section>

<section class="uses">
  <h2>What do you need or can use a report for</h2>
  <ul class="use-list">
    <li>Buying/selling shares or entire companies</li>
    <li>Inheritance matters</li>
    <li>Questions in gain compensations (in divorce)</li>
  </ul>
</section>

<section class="reasons">
  <h2>Why you should work with me</h2>
  <div class="connector" style="left:339px"></div>
  <div class="connector" style="left:700px"></div>
  <div class="reason" style="left:91px">
    <svg viewBox="0 0 124 124" fill="none" stroke="#fff" stroke-width="5"><circle cx="62" cy="62" r="56"/><path d="M62 22v40l-22 18" stroke-linecap="round"/></svg>
    <div class="num">01</div><h3>Schnell</h3>
    <p>Sie bekommen Ihr Gutachten zeitnah (innerhalb von max. 21 Tagen nach Zugang aller benötigten Unterlagen)</p>
  </div>
  <div class="reason" style="left:447px">
    <svg viewBox="0 0 124 124" fill="none" stroke="#fff" stroke-width="5" stroke-linejoin="round"><path d="M62 6l46 16v36c0 30-20 50-46 60C36 108 16 88 16 58V22z"/><path d="M40 62l16 16 30-32" stroke-linecap="round"/></svg>
    <div class="num">02</div><h3>Zertifiziert</h3>
    <p>Sie erhalten ein qualifiziertes und belastbares Gutachten von einem zertifizierten Sachverständigen (höchste Akzeptanz bei allen Parteien)</p>
  </div>
  <div class="reason" style="left:805px">
    <svg viewBox="0 0 124 124" fill="none" stroke="#fff" stroke-width="5" stroke-linejoin="round"><path d="M20 6h60l20 20v92H20z"/><path d="M34 34h40M34 50h30M34 66h20" stroke-linecap="round"/><circle cx="78" cy="78" r="16"/><path d="M90 90l18 18" stroke-linecap="round" stroke-width="7"/></svg>
    <div class="num">03</div><h3>Verständlich</h3>
    <p>Ihr Gutachten wird für Sie logisch und nachvollziehbar sein und kein "Fachchinesisch" enthalten</p>
  </div>
</section>

<section class="promise">
  <div class="mark">ARNO VELDEN</div>
  <h2>Mein Qualitätsversprechen:</h2>
  <p>Sollte der avisierte Termin für die Erstellung des Gutachtens überschritten<br>werden, erhalten Sie das Gutachten absolut kostenfrei!<br>(Ich verzichte auf mein Honorar)</p>
</section>

<section class="whw">
  <div class="whw-track"></div>
  <div class="ring" style="top:76px"><div class="inner">WHY</div></div>
  <div class="ring-dot" style="top:512px"></div>
  <div class="ring" style="top:402px"><div class="inner">HOW</div></div>
  <div class="ring-dot" style="top:822px"></div>
  <div class="ring" style="top:717px"><div class="inner">WHAT</div></div>
  <div class="whw-text" style="top:110px"><h3>Why I do, what I do</h3><p>Economy is my passion. Economy is made in numbers. Sometimes it is difficult to find the right numbers.</p></div>
  <div class="whw-text" style="top:440px"><h3>How I do, what I do</h3><p>Jedes Gutachten beginnt mit Verstehen. Also stelle ich Ihnen&nbsp; Fragen und höre sehr genau zu.</p></div>
  <div class="whw-text" style="top:752px"><h3>What I do</h3><p>Conducting business valuations in case of ...<br>Durchführung von Unternehmensbewertungen<br>(Wertermittlung) bei</p></div>
</section>

<section class="about">
  <h2>About Me ( Arno K. Velden)</h2>
  <div class="about-photo" role="img" aria-label="Foto des Sachverständigen am Schreibtisch in einem hellen Büro"></div>
  <div class="about-frame"></div>
  <div class="about-card">
    <div class="col-main">
      <div class="block"><h4>Professional Experience</h4>
        10 years as managing director in the fitness market<br>10 years as CMO / business trainer / CEO in an german industrial company (fitness industry)<br>outside lecturer at AHSF<br>expert VSBX</div>
      <div class="block"><h4>Educations</h4>
        Bankkaufmann KHV<br>staatl. Geprüfter Betriebswirt (BA)<br>Dipl.-Kfm. (FH)<br>Business Trainer BTVN<br>Lizenzierter Fitnesstrainer FSVD<br>Sachverständiger für Unternehmensbewertungen</div>
    </div>
    <div class="col-side">
      <div class="block"><h4>Field of Activity</h4>
        Appraisals Company Valuation<br>Marketing<br>Strategic Corporate Governance<br>Corporate Health Management<br>Change Management</div>
      <h4>Partners</h4>
      <div class="badge"></div>
      <div class="badge small"></div>
    </div>
  </div>
</section>

<section class="contact">
  <h2>Contact Us</h2>
  <div class="field" style="left:127px;top:174px;width:463px">Name</div>
  <div class="field" style="left:610px;top:174px;width:459px">Email</div>
  <div class="field" style="left:127px;top:231px;width:463px">Phone Number</div>
  <div class="field" style="left:610px;top:231px;width:459px">Appointments</div>
  <div class="field tall" style="left:127px;top:288px;width:942px">Messages</div>
  <div class="submit">Submit</div>
</section>

<footer class="footer">
  <div class="brand"><span class="dot"></span>Arno Velden</div>
  <div class="links"><h3>Quick Link</h3>
    <ul><li>Home</li><li>What I Do</li><li>Why I Do It &amp; How I Do It</li><li>About Me</li><li>Contact</li></ul></div>
  <div class="news"><h3>Newsletter</h3>
    <p>Register your email for news for Arno Velden</p>
    <div class="in">Enter the email</div>
    <div class="btn">Submit</div></div>
  <div class="copy">Copyright © 2018 Arno Velden All Rights Reserved.</div>
</footer>

</body>
</html>
```